Specialised investor in e-mobility and energy wants business card design

We need a business card design that fits our existing corporate design. <The look and feel must be 'sharp'/'clean', dynamic, communicate momentum, professionalism etc (as one would imagine from a firm in the financial sector). We like the idea of a reverse-side of the card that includes the logo, and the name and contact details on the other. We expect the deliverable to be whatever format might be required to be able to get cards printed directly by a service such as kelmo press. Our website is www.zub.capital

```html
<!DOCTYPE html>
<html lang="en">
<head>
<meta charset="utf-8">
<title>ZUB Capital – Business Card</title>
<link href="https://fonts.googleapis.com/css2?family=Lato:wght@400;700;900&display=swap" rel="stylesheet">
<style>
  :root {
    --bg: #2b2b2b;
    --paper: #ffffff;
    --green-dark: #334f22;
    --green-light: #7ab648;
    --ink-light: #ffffff;
  }
  html, body {
    margin: 0;
    padding: 0;
    width: 1200px;
    height: 875px;
    overflow: hidden;
    background: var(--bg);
    font-family: "Lato", Arial, sans-serif;
  }
  .canvas {
    position: relative;
    width: 1200px;
    height: 875px;
  }
  .card {
    position: absolute;
    left: 320px;
    width: 560px;
    height: 320px;
    background: var(--paper);
    overflow: hidden;
    box-shadow: 0 18px 40px rgba(0,0,0,.45);
  }
  .card--front { top: 95px; }
  .card--back { top: 460px; }

  .card__shapes {
    position: absolute;
    inset: 0;
    width: 100%;
    height: 100%;
  }

  .brand {
    position: absolute;
    display: flex;
    align-items: center;
    gap: 12px;
    color: var(--green-dark);
    font-weight: 400;
    white-space: nowrap;
  }
  .brand__dot {
    border-radius: 50%;
    background: var(--green-light);
  }
  .card--front .brand {
    left: 0; right: 0;
    top: 108px;
    justify-content: center;
    font-size: 64px;
    letter-spacing: 1px;
  }
  .card--front .brand__dot { width: 22px; height: 22px; }

  .card--back .brand {
    right: 38px;
    top: 68px;
    font-size: 34px;
    gap: 8px;
  }
  .card--back .brand__dot { width: 12px; height: 12px; }

  .contact {
    position: absolute;
    left: 34px;
    bottom: 34px;
    color: var(--ink-light);
  }
  .contact__name {
    margin: 0;
    font-size: 24px;
    font-weight: 900;
    letter-spacing: .5px;
    text-transform: uppercase;
  }
  .contact__role {
    margin: 2px 0 18px;
    font-size: 15px;
    color: var(--green-light);
  }
  .contact__list {
    list-style: none;
    margin: 0;
    padding: 0;
    font-size: 12.5px;
    line-height: 1.5;
  }
  .contact__item {
    display: flex;
    align-items: flex-start;
    gap: 9px;
  }
  .contact__icon {
    width: 11px;
    height: 11px;
    margin-top: 3px;
    flex: none;
    fill: var(--green-light);
  }
</style>
</head>
<body>
<main class="canvas">

  <section class="card card--front" aria-label="Business card front">
    <svg class="card__shapes" viewBox="0 0 560 320" preserveAspectRatio="none" aria-hidden="true">
      <polygon points="0,306 330,306 322,320 0,320" fill="var(--green-dark)"/>
      <polygon points="336,306 560,306 560,320 328,320" fill="var(--green-light)"/>
    </svg>
    <div class="brand">
      <span class="brand__dot"></span>
      <span class="brand__name">ZUB Capital</span>
    </div>
  </section>

  <section class="card card--back" aria-label="Business card back">
    <svg class="card__shapes" viewBox="0 0 560 320" preserveAspectRatio="none" aria-hidden="true">
      <polygon points="0,0 225,0 390,320 0,320" fill="var(--green-dark)"/>
      <polygon points="231,0 241,0 406,320 396,320" fill="var(--green-light)"/>
    </svg>

    <div class="brand">
      <span class="brand__dot"></span>
      <span class="brand__name">ZUB Capital</span>
    </div>

    <div class="contact">
      <h1 class="contact__name">Marcus Fenwick</h1>
      <p class="contact__role">Founder &amp; CEO</p>
      <ul class="contact__list">
        <li class="contact__item">
          <svg class="contact__icon" viewBox="0 0 12 12"><path d="M6 0a4 4 0 0 0-4 4c0 3 4 8 4 8s4-5 4-8a4 4 0 0 0-4-4zm0 5.6a1.6 1.6 0 1 1 0-3.2 1.6 1.6 0 0 1 0 3.2z"/></svg>
          <span>ZUB Capital S.A.<br>Lausanne, Switzerland</span>
        </li>
        <li class="contact__item">
          <svg class="contact__icon" viewBox="0 0 12 12"><path d="M3 0h6a1 1 0 0 1 1 1v10a1 1 0 0 1-1 1H3a1 1 0 0 1-1-1V1a1 1 0 0 1 1-1zm0 1.5v8h6v-8z"/></svg>
          <span>+41 79555 0148</span>
        </li>
        <li class="contact__item">
          <svg class="contact__icon" viewBox="0 0 12 12"><path d="M0 2h12v8H0zm1 1v.3l5 3.4 5-3.4V3z"/></svg>
          <span>marcus@zub.capital</span>
        </li>
        <li class="contact__item">
          <svg class="contact__icon" viewBox="0 0 12 12"><circle cx="6" cy="6" r="5.5"/><path d="M.5 6h11M6 .5c2.5 3 2.5 8 0 11M6 .5c-2.5 3-2.5 8 0 11" stroke="var(--green-dark)" stroke-width="1" fill="none"/></svg>
          <span>www.zub.capital</span>
        </li>
      </ul>
    </div>
  </section>

</main>
</body>
</html>
```